Website for new dental office

I am Dr. Colin Ashford and am building a new dental practice. I specialize in general dentistry. I am young and have a higher end dental practice incorporating very new technologies and would like my website to reflect that. As many dental patients are older, the website must be very easy to navigate. I would like patients to be able to request appointments, and will eventually add on patient information forms (the health history, etc, that you normally fill out in the practice) from my practice management software, so leave an area for that.

Industry/Entity Type

Building

```html
<!DOCTYPE html>
<html lang="en">
<head>
<meta charset="utf-8">
<title>Ashford Dental Clinic</title>
<link href="https://fonts.googleapis.com/css2?family=Open+Sans:wght@300;400;600&display=swap" rel="stylesheet">
<style>
:root{
  --green:#10a552;
  --green-dark:#0d8f46;
  --ink:#333;
  --muted:#6a6a6a;
  --light:#999;
  --band:#dfe1e2;
  --panel:#ececec;
  --footer:#3b3b3b;
  --social:#666;
  --white:#fff;
}
*{box-sizing:border-box;margin:0;padding:0}
html,body{width:920px;height:1200px;overflow:hidden;background:var(--white)}
body{position:relative;font-family:"Open Sans",Arial,sans-serif;color:var(--ink)}
.abs{position:absolute}
.brand{left:75px;top:18px;font-size:32px;font-weight:400;color:var(--green);letter-spacing:-.5px}
.call{right:106px;top:20px;text-align:right;line-height:1}
.call small{display:block;font-size:12px;color:var(--muted);margin-bottom:3px}
.call strong{font-size:17px;font-weight:400;color:#222}
.call-icon{left:820px;top:28px}
.hero-band{left:0;top:90px;width:920px;height:370px;background:var(--band)}
.nav{left:76px;top:72px;width:768px;height:36px;background:var(--green);display:flex;align-items:center;border-radius:2px}
.nav a{height:36px;line-height:36px;padding:0 15px;font-size:11.5px;color:var(--white);text-decoration:none;border-right:1px solid var(--green-dark)}
.nav a.active{background:#3d3d3d;padding:0 18px}
.search{left:740px;top:78px;width:98px;height:24px;background:var(--white);border-radius:2px;font-size:10px;color:var(--light);padding:5px 8px}
.search svg{position:absolute;right:5px;top:4px}
.hero{left:76px;top:108px;width:768px;height:352px;background:linear-gradient(120deg,#eef1f3 0%,#d8dfe6 30%,#9cb4cf 45%,#e9edf0 70%,#f4f5f6 100%)}
.caption{left:326px;top:128px;background:rgba(255,255,255,.7);padding:6px 14px;font-size:19px;line-height:24px;color:#555;white-space:nowrap}
.arrow{top:262px}
.col-title{top:478px;font-size:16px;font-weight:400;color:var(--green)}
.col-bar{top:504px;width:240px;height:3px;background:var(--green)}
.col-img{top:507px;width:240px;height:142px}
.divider{left:77px;top:672px;width:767px;height:1px;background:#ddd}
.welcome{left:79px;top:693px;font-size:18.5px;font-weight:400;color:var(--green)}
.intro{left:79px;top:723px;width:496px;font-size:10.3px;line-height:17.6px;color:var(--muted)}
.news-title{left:632px;top:693px;font-size:16.5px;font-weight:400;color:var(--green)}
.news-icon{left:603px;top:697px}
.date{left:603px;width:39px;height:62px;background:var(--green);color:var(--white);text-align:center;padding-top:16px}
.date i{display:block;font-size:8.5px;font-style:italic}
.date b{display:block;font-size:16px;font-weight:400;line-height:18px}
.news-text{left:650px;width:190px;font-size:9.3px;line-height:14.4px;color:#222}
.news-text span{display:block;margin-top:3px;color:var(--light)}
.appt{left:76px;top:886px;width:768px;height:214px;background:var(--panel)}
.appt h2{position:absolute;left:0;width:100%;top:15px;text-align:center;font-size:14.4px;font-weight:400;color:#222}
.field{height:30px;background:var(--white);border:1px solid #ddd;font-size:10px;color:var(--muted);padding:8px 13px}
.submit{left:421px;top:1050px;width:78px;height:29px;background:linear-gradient(#8a8a8a,#6c6c6c);color:var(--white);font-size:12.5px;text-align:center;line-height:29px;border-radius:2px}
.footer{left:0;top:1122px;width:920px;height:78px;background:var(--footer)}
.flinks{left:78px;top:1139px;font-size:10px;color:#ddd;word-spacing:2px}
.copy{left:78px;top:1167px;font-size:9.6px;color:#ccc;word-spacing:2px}
.social{top:1150px}
</style>
</head>
<body>
<div class="abs brand">Ashford Dental Clinic</div>
<div class="abs call"><small>Call us</small><strong>555 014 2297</strong></div>
<svg class="abs call-icon" width="24" height="22" viewBox="0 0 24 22"><path d="M3 3c2-2 4 1 5 3s-1 3 0 5 3 3 5 4 3-2 5 0 2 3 0 5C14 22 0 9 3 3z" fill="#555"/><path d="M16 4a5 5 0 0 1 4 4M16 1a8 8 0 0 1 7 7" stroke="#777" fill="none" stroke-width="1.2"/></svg>

<div class="abs hero-band"></div>
<div class="abs hero" role="img" aria-label="Photo of a young dentist in blue scrubs with his team and a patient in a modern treatment room"></div>
<div class="abs caption">Dr. Colin Ashford is specialised<br>in general dentistry</div>
<svg class="abs arrow" style="left:76px" width="28" height="28" viewBox="0 0 28 28"><circle cx="14" cy="14" r="14" fill="#8d8d8d"/><path d="M16 8l-6 6 6 6" stroke="#fff" stroke-width="3" fill="none"/></svg>
<svg class="abs arrow" style="left:815px" width="28" height="28" viewBox="0 0 28 28"><circle cx="14" cy="14" r="14" fill="#8d8d8d"/><path d="M12 8l6 6-6 6" stroke="#fff" stroke-width="3" fill="none"/></svg>

<nav class="abs nav">
  <a class="active">HOME</a><a>ABOUT US</a><a>SERVICES</a><a>FACILITIES</a><a>PRACTICES</a><a>TESTIMONIALS</a><a>CONTACT US</a>
</nav>
<div class="abs search">Search<svg width="16" height="16" viewBox="0 0 16 16"><circle cx="6.5" cy="6.5" r="4.5" stroke="#888" stroke-width="2" fill="none"/><path d="M10 10l4 4" stroke="#888" stroke-width="2.4"/></svg></div>

<h3 class="abs col-title" style="left:79px">About Dr. Colin Ashford</h3>
<div class="abs col-bar" style="left:78px"></div>
<div class="abs col-img" style="left:78px;background:linear-gradient(135deg,#c9d3d9,#a9bac6 60%,#d7dde0)" role="img" aria-label="Photo of a smiling older man holding a red apple"></div>

<h3 class="abs col-title" style="left:343px">Dental Services</h3>
<div class="abs col-bar" style="left:341px"></div>
<div class="abs col-img" style="left:341px;background:linear-gradient(135deg,#c99c86,#e6d8d2 45%,#7aa3d6)" role="img" aria-label="Photo of a patient having a dental check-up with mirror and probe"></div>

<h3 class="abs col-title" style="left:605px">Dental Practices</h3>
<div class="abs col-bar" style="left:603px"></div>
<div class="abs col-img" style="left:603px;background:linear-gradient(135deg,#e8ecef,#c9d4de 50%,#4f7ec2)" role="img" aria-label="Photo of two dentists treating a patient"></div>

<div class="abs divider"></div>

<h2 class="abs welcome">Welcome to Ashford Dental Clinic</h2>
<p class="abs intro">Nulla molestie dui at sem pretium, vitae adipiscing metus pellentesque. Quisque a justo congue, molestie urna at, venenatis felis. In hac habitasse platea dictumst. Sed euismod mollis tellus sit amet mollis. Donec varius lorem eu tellus feugiat, vel semper neque facilisis. Fusce at nisi bibendum, euismod sapien nec, convallis lacus. Nunc nec nulla fermentum, ultricies sapien dignissim, mattis mi. Pellentesque vitae felis iaculis, tristique purus ac, cursus eros. Fusce a adipiscing tellus. Class aptent taciti sociosqu ad litora torquent per conubia nostra, per inceptos himenaeos. Nunc fermentum dolor in mi fringilla tincidunt. Cras massa nunc, dictum in eros a, fermentum imperdiet mi. Integer tincidunt lorem sed posuere convallis.</p>

<svg class="abs news-icon" width="20" height="16" viewBox="0 0 20 16"><rect x="1" y="1" width="18" height="14" fill="none" stroke="#10a552" stroke-width="2"/><rect x="4" y="4" width="5" height="5" fill="#10a552"/><path d="M11 5h5M11 8h5M4 11h12" stroke="#10a552" stroke-width="1.5"/></svg>
<h2 class="abs news-title">Latest News</h2>

<div class="abs date" style="top:728px"><i>Apr</i><b>26</b></div>
<div class="abs news-text" style="top:729px">Quisque at tincidunt odio. Ut justo odio, tristique viverra neque porttitor, luctus mollis nulla commodo nisl orc.<span>READ MORE</span></div>
<div class="abs date" style="top:801px"><i>Apr</i><b>26</b></div>
<div class="abs news-text" style="top:802px">Quisque at tincidunt odio. Ut justo odio, tristique viverra neque porttitor, luctus mollis nulla commodo nisl orc.<span>READ MORE</span></div>

<section class="abs appt"><h2>REQUEST AN APPOINTMENT</h2></section>
<div class="abs field" style="left:85px;top:935px;width:174px">Name</div>
<div class="abs field" style="left:276px;top:935px;width:174px">E-mail</div>
<div class="abs field" style="left:469px;top:935px;width:174px">Phone</div>
<div class="abs field" style="left:660px;top:935px;width:174px">Service for<svg style="position:absolute;right:8px;top:12px" width="9" height="5"><path d="M0 0h9L4.5 5z" fill="#888"/></svg></div>
<div class="abs field" style="left:85px;top:974px;width:750px;height:62px">Message</div>
<div class="abs submit">SUBMIT</div>

<footer class="abs footer"></footer>
<div class="abs flinks">Home &nbsp;| &nbsp;About us &nbsp;| &nbsp;Services &nbsp;| &nbsp;Facilities &nbsp;| &nbsp;Practices &nbsp;| &nbsp;Testimonials &nbsp;| &nbsp;contact us</div>
<div class="abs copy">Copyright © 2014 &nbsp;Ashford Dental Clinic. &nbsp;All rights reserved.</div>
<svg class="abs social" style="left:744px" width="20" height="20" viewBox="0 0 20 20" aria-label="Share"><circle cx="10" cy="10" r="10" fill="#666"/><circle cx="6.5" cy="10" r="1.7" fill="#3b3b3b"/><circle cx="13.5" cy="6.5" r="1.7" fill="#3b3b3b"/><circle cx="13.5" cy="13.5" r="1.7" fill="#3b3b3b"/><path d="M6.5 10l7-3.5M6.5 10l7 3.5" stroke="#3b3b3b" stroke-width="1.1"/></svg>
<svg class="abs social" style="left:771px" width="20" height="20" viewBox="0 0 20 20" aria-label="Chat"><circle cx="10" cy="10" r="10" fill="#666"/><path d="M5 6h10v6H9l-3 2.5V12H5z" fill="none" stroke="#3b3b3b" stroke-width="1.3" stroke-linejoin="round"/></svg>
<svg class="abs social" style="left:798px" width="20" height="20" viewBox="0 0 20 20" aria-label="Website"><circle cx="10" cy="10" r="10" fill="#666"/><circle cx="10" cy="10" r="5" fill="none" stroke="#3b3b3b" stroke-width="1.2"/><ellipse cx="10" cy="10" rx="2" ry="5" fill="none" stroke="#3b3b3b" stroke-width="1"/><path d="M5 10h10" stroke="#3b3b3b" stroke-width="1"/></svg>
<svg class="abs social" style="left:824px" width="20" height="20" viewBox="0 0 20 20" aria-label="Email"><circle cx="10" cy="10" r="10" fill="#666"/><rect x="5" y="6.5" width="10" height="7" fill="none" stroke="#3b3b3b" stroke-width="1.3"/><path d="M5 6.5l5 4 5-4" fill="none" stroke="#3b3b3b" stroke-width="1.3"/></svg>
</body>
</html>
```